Lotstallmart.com Webpage Design

Design Brief for lotstallmart.com (Copy of Brief also in attached Word file)

Name of Website- lotstallmart.com (existing logo and look & feel of website to be changed)

Logo - Finalised. The logo files are attached with the brief as “logo.jpeg”. The “Blue- Grey” version of the logo is for use on lighter backgrounds and the “Orange-White” version of the logo is for use on darker backgrounds. (A full Black version of the logo is also attached). Both versions may be used in different parts of the website. All attached files are in .png format.
Status - The website in functional and is undergoing user trials. However, we want to improve the look & feel of the website so at it seems
a. cotemporary,
b. Easy to Navigate
c. professional and
d. Vibrant.

Please visit ‘lotstallmart.com’ to check out the website and its functionalities – please use it only as a reference for the features & functions to be provided, however the designer should use a ‘Free Hand’ in designing the composition of various parts of the webpage without getting too influenced by the existing design

Objective of the Website ‘lotstallmart.com –
a. It is a portal focussed on listing of ‘Retail’ specific real-estate properties by developers, owners and realty brokers. The properties shall listed under the following four categories-
i. Retail Malls
ii. Shopping Complexes
iii. High-street shops
iv. Retail Warehouses
*refer lotstallmart.com for better clarity

b. The abovementioned properties shall be listed either for ‘Sale’ or ‘rent\lease’ or both

c. Users shall visit the site in case they wish to acquire a retail \ shop space either on ‘sale’ or ‘rent’. These Users would be able to specify the ‘Search Criteria’ through the tool-bars provided on the website – the ‘Search Criteria’ shall comprise of ‘Type of space category’, ‘City’, ‘Locality’, transaction type ie ‘Rent \ Sale’ and ‘Area Range’

d. The main revenue model for the website shall be listing fee ( or advertising charges ) payable by those listing their properties on the website.

Three Main Pages of Website (lotstallmart.com) that need to be designed -
a. Main Home Page (visit the web link - http://lotstallmart.com/ ) - The main home page has the “Search Toolbar” for specifying of Search Criteria by the User. It shall also have the following features & functions-
i. Main Advertising Banner
ii. Featured Projects
iii. New Launches
iv. Toolbar with buttons – ‘Advertise with Us’, ‘Listings Alert’, ‘Mart Wizards’, ‘Advertiser Login’

b. Property Listings Page (visit the web link - http://lotstallmart.com/gurgaon-in-india ) - The List of property options that match the Criteria specified by the ‘User’ get displayed on this page.

c. Property Detail Page - When the ‘User’ clicks on the “More….” Button on the ‘Property Listings Page’ (given in point b. above) the web page with the details of the property opens. (For Example – visit the web link - http://lotstallmart.com/vorne-Shopping-Complex-vorne-quadrion-gurgaon-636 )

Note:- Please refer to attached ‘Shopping’ related images the designer may use them on the website to provide a look & feel of retail if required – either separately or rotate in a single window

Target Market(s)

Retailers & Investors looking for retail space, Real Estate Brokers, Developers

Industry/Entity Type

Advertising

Number of Pages Required

3 page

Requirements
Must have
• Refer to existing site lotstallmart.com -- all the existing functionalities are a must have.
Nice to have
• The Designer may use the retail related images on the website if required for making it more vibrant. Refer attached images Shopping(1-6).jpg

```html
<!DOCTYPE html>
<html lang="en">
<head>
<meta charset="utf-8">
<title>Lotstallmart.com – India's Leading Portal for Retail Space</title>
<link href="https://fonts.googleapis.com/css2?family=Open+Sans:wght@300;400;600;700&display=swap" rel="stylesheet">
<style>
:root{
  --blue:#0aa2ef;
  --ink:#333;
  --grey-bar:#e4e4e4;
  --login-bg:#55585d;
  --panel:rgba(20,20,20,.88);
  --section-bg:#efefef;
  --card-border:#dedede;
  --footer:#2f2f31;
  --footer-dark:#222224;
  --footer-text:#b9b9b9;
  --yellow:#f4c430;
}
*{box-sizing:border-box;margin:0;padding:0}
html,body{width:1200px;height:2378px;overflow:hidden}
body{font-family:"Open Sans",Arial,sans-serif;color:var(--ink);background:#fff;position:relative}
.wrap{position:absolute;left:118px;width:964px}

/* city strip */
.city-strip{position:absolute;top:0;left:0;width:1200px;height:38px;background:var(--grey-bar);display:flex;justify-content:center;align-items:center;font-size:12.5px;color:#666}
.city-strip span{padding:0 11px;border-right:1px solid #aaa;line-height:13px}
.city-strip span:last-child{border:none}

/* header */
.site-header{position:absolute;top:38px;left:0;width:1200px;height:136px}
.brand{position:absolute;left:119px;top:38px;display:flex;align-items:center;gap:10px}
.brand-dot{width:30px;height:30px;border-radius:50%;background:var(--blue)}
.brand-name{font-size:33px;font-weight:700;color:#4a4f55;letter-spacing:-.5px;line-height:1}
.brand-tag{position:absolute;left:159px;top:78px;font-size:9px;font-weight:700;color:#555;letter-spacing:.3px}
.main-nav{position:absolute;left:507px;top:46px;display:flex}
.main-nav a{display:block;text-decoration:none;text-align:center;padding:4px 18px 6px;border-right:1px solid #ddd;color:var(--blue);font-size:17px;line-height:20px}
.main-nav a small{display:block;font-size:11px;color:#999;line-height:14px}
.main-nav a.active{border:1px solid #ccc;padding:4px 14px 6px;margin-right:18px}

/* advertiser strip */
.ad-strip{position:absolute;top:174px;left:0;width:1200px;height:53px;background:var(--blue);display:flex;justify-content:center;align-items:center;color:#fff;font-size:13px}
.ad-strip span{padding:0 12px}
.ad-strip .login{font-weight:600;font-size:14.5px;border-left:1px solid #7fd0fa;border-right:1px solid #7fd0fa;display:flex;align-items:center;gap:6px}
.ad-strip .caret{position:absolute;left:592px;top:45px;width:0;height:0;border-left:9px solid transparent;border-right:9px solid transparent;border-bottom:9px solid var(--login-bg)}

/* login bar */
.login-bar{position:absolute;top:227px;left:0;width:1200px;height:93px;background:var(--login-bg)}
.login-bar .field{position:absolute;top:27px;height:38px;background:#fff;padding:0 16px;font-size:13.5px;color:#999;display:flex;align-items:center}
.login-bar .btn-sign{position:absolute;left:592px;top:27px;width:75px;height:38px;background:var(--blue);color:#fff;font-size:15px;font-weight:600;display:flex;align-items:center;justify-content:center}
.login-bar .remember{position:absolute;left:692px;top:37px;color:#fff;font-size:13px;display:flex;align-items:center;gap:8px}
.login-bar .box{width:12px;height:12px;background:#fff}
.login-bar .forgot{position:absolute;left:836px;top:37px;color:#fff;font-size:12.5px}
.login-bar .new{position:absolute;left:962px;top:20px;color:#fff;font-size:12px}
.login-bar .btn-register{position:absolute;left:962px;top:38px;width:94px;height:25px;background:#ddd;color:#444;font-size:10px;display:flex;align-items:center;justify-content:center}

/* hero */
.hero{position:absolute;top:320px;left:0;width:1200px;height:569px;background:linear-gradient(100deg,#5a4a3d 0%,#8c7660 22%,#b9a68e 40%,#c9b18b 55%,#7d6a58 75%,#4c3f36 100%)}
.hero-arrow{position:absolute;top:268px;width:34px;height:34px;background:#1e1e1e;display:flex;align-items:center;justify-content:center}
.search-panel{position:absolute;left:117px;top:21px;width:311px;height:528px;background:var(--panel);color:#fff;padding:0 22px}
.search-panel .label{font-size:13px;margin-top:18px}
.search-panel .meaning{font-size:14px;color:var(--yellow)}
.search-panel .checks{display:grid;grid-template-columns:1fr 1fr;row-gap:14px;margin:14px -22px 0;font-size:11.5px;padding:0 0 18px 22px;border-bottom:1px solid #444}
.search-panel .checks span{display:flex;align-items:center;gap:8px}
.search-panel .checks i{width:11px;height:11px;background:#eee;display:block}
.select{height:38px;background:#fff;color:#333;font-size:12.5px;display:flex;align-items:center;padding:0 14px;position:relative;margin-top:9px}
.select::after{content:"";position:absolute;right:14px;top:16px;border-left:7px solid transparent;border-right:7px solid transparent;border-top:7px solid #333}
.select.keyword{color:#999;padding-right:30px}
.select.keyword::after{display:none}
.search-panel .lbl{font-size:12.5px;margin-top:22px}
.btn-search{position:absolute;right:22px;bottom:18px;width:80px;height:34px;background:var(--blue);font-size:15px;display:flex;align-items:center;justify-content:center}

/* categories */
.categories{top:889px;height:94px;display:flex;align-items:center;border-bottom:2px solid #e3e3e3}
.cat{flex:none;display:flex;gap:10px;padding-left:32px;border-right:1px solid #ddd;height:52px;align-items:flex-start;white-space:nowrap}
.cat:first-child{padding-left:15px}
.cat:last-child{border:none}
.cat h3{color:var(--blue);font-size:18.5px;font-weight:600;line-height:22px}
.cat p{font-size:11.5px;color:#666;margin-left:2px}
.tick{width:22px;height:22px;border-radius:50%;background:var(--blue);flex:none;margin-top:3px;display:flex;align-items:center;justify-content:center}

/* project sections */
.projects{background:var(--section-bg);padding:0 15px}
.projects h2{font-size:23px;font-weight:400;color:var(--blue);height:63px;display:flex;align-items:center;letter-spacing:.3px}
.projects .more{position:absolute;right:15px;top:24px;width:19px;height:19px;border-radius:50%;border:2px solid #666;display:flex;align-items:center;justify-content:center}
.cards{display:flex;gap:13px}
.card{width:176px;height:215px;background:#fff;border:1px solid var(--card-border);text-align:center;padding-top:10px}
.card .thumb{width:158px;height:111px;margin:0 auto}
.card .name{font-size:13.5px;margin-top:11px;color:#222}
.card .city{font-size:13.5px;color:var(--blue);margin-top:5px}
.card .type{font-size:11.5px;color:#666;margin-top:5px}

/* newsletter */
.newsletter{position:absolute;top:1972px;left:0;width:1200px;height:79px;background:var(--blue)}
.newsletter h2{position:absolute;left:120px;top:20px;font-size:31px;font-weight:300;color:#fff;letter-spacing:.5px}
.newsletter .input{position:absolute;top:23px;height:34px;background:#fff;font-size:14px;color:#444;display:flex;align-items:center;padding:0 14px}
.newsletter .dd::after{content:"";position:absolute;right:12px;top:14px;border-left:6px solid transparent;border-right:6px solid transparent;border-top:6px solid #888}
.btn-subscribe{position:absolute;left:979px;top:23px;width:98px;height:34px;background:#1c1c1c;color:#fff;font-size:15px;display:flex;align-items:center;justify-content:center}

/* footer */
.site-footer{position:absolute;top:2051px;left:0;width:1200px;height:252px;background:var(--footer)}
.fcol{position:absolute;top:36px;color:var(--footer-text);font-size:12px}
.fcol h4{color:#ddd;font-size:14px;font-weight:600;margin-bottom:20px}
.fcol ul{list-style:none;line-height:24.5px}
.fcol ul li::before{content:"• "}
.fcol.sep{border-left:1px solid #4a4a4c;padding-left:22px;height:150px}
.fcol .about{line-height:21px;color:#9d9d9d;font-size:12.5px;width:215px}
.contact-row{display:flex;gap:14px;align-items:flex-start;line-height:21px;margin-bottom:12px;font-size:12.5px}
.contact-row svg{flex:none;margin-top:4px}
.wizard-form{position:absolute;left:848px;top:36px;width:232px;height:200px;border-left:1px solid #4a4a4c;color:var(--footer-text)}
.wizard-form h4{color:#ddd;font-size:14px;font-weight:600;margin:0 0 16px 22px}
.f-input{width:206px;height:34px;background:#1f1f21;color:#777;font-size:11px;padding:0 14px;display:flex;align-items:center;margin:0 0 7px 22px}
.btn-submit{position:absolute;right:2px;top:164px;width:62px;height:26px;background:#6a6a6c;color:#fff;font-size:11px;display:flex;align-items:center;justify-content:center}

.bottom-bar{position:absolute;top:2303px;left:0;width:1200px;height:75px;background:var(--footer-dark)}
.bottom-bar p{position:absolute;left:120px;top:29px;font-size:11.5px;color:#999}
.social{position:absolute;left:842px;top:21px;display:flex;gap:8px}
.social span{width:31px;height:31px;border-radius:50%;background:#5e6266;display:block}
</style>
</head>
<body>

<nav class="city-strip">
  <span>Bangalore</span><span>Chennai</span><span>Greater Noida</span><span>Gurgaon</span><span>Hyderabad</span><span>Jaipur</span><span>Khanna</span><span>Kolkatta</span><span>Mumbai</span><span>Noida</span><span>Pune</span><span>Surat</span><span>More</span>
</nav>

<header class="site-header">
  <div class="brand"><span class="brand-dot"></span><span class="brand-name">lotstallmart.com</span></div>
  <div class="brand-tag">INDIA'S LEADING PORTAL FOR RETAIL SPACE</div>
  <nav class="main-nav">
    <a class="active" href="#">HOME<small>Welcome</small></a>
    <a href="#">ADVERTISE WITH US<small>Standard listing - FREE</small></a>
    <a href="#">MART WIZARDS<small>Shop Search Services</small></a>
    <a href="#">LISTING ALERT<small>Newsletter Subscribe</small></a>
  </nav>
</header>

<div class="ad-strip">
  <span>List your Property Here</span>
  <span class="login">
    <svg width="10" height="11" viewBox="0 0 10 11"><circle cx="5" cy="3" r="2.6" fill="#fff"/><path d="M0 11c0-3.5 2.2-5 5-5s5 1.5 5 5z" fill="#fff"/></svg>
    ADVERTISER LOGIN</span>
  <span>New Advertiser - Register</span>
  <i class="caret"></i>
</div>

<section class="login-bar">
  <div class="field" style="left:141px;width:215px">Username</div>
  <div class="field" style="left:367px;width:214px">Password</div>
  <div class="btn-sign">SIGN IN</div>
  <div class="remember"><i class="box"></i>Keep me logged in</div>
  <div class="forgot">Forgot Password</div>
  <div class="new">New Advertiser?</div>
  <div class="btn-register">REGISTER</div>
</section>

<section class="hero" role="img" aria-label="Banner photograph: a family with shopping bags in front of a store window with sale signs">
  <div class="hero-arrow" style="left:0"><svg width="14" height="12" viewBox="0 0 14 12"><path d="M6 0 0 6l6 6V8h8V4H6z" fill="#fff"/></svg></div>
  <div class="hero-arrow" style="right:0"><svg width="14" height="12" viewBox="0 0 14 12"><path d="M8 0l6 6-6 6V8H0V4h8z" fill="#fff"/></svg></div>

  <form class="search-panel">
    <div class="label">Select Retail Format :</div>
    <div class="meaning">Meaning of Retail Format</div>
    <div class="checks">
      <span><i></i>Retail Mall</span><span><i></i>Shopping Complex</span>
      <span><i></i>High Street Shops</span><span><i></i>Retail Warehouses</span>
    </div>
    <div class="lbl">Sale Or Rent Or Both :</div>
    <div class="select">Both</div>
    <div class="lbl">Select City :</div>
    <div class="select">Select</div>
    <div class="lbl">Select Locality/Micro-Market.</div>
    <div class="select">Select</div>
    <div class="lbl">Enter Keyword :</div>
    <div class="select keyword">Name of Project or Developet etc
      <svg style="position:absolute;right:10px;top:11px" width="16" height="16" viewBox="0 0 16 16"><circle cx="6.5" cy="6.5" r="5" stroke="#333" stroke-width="2" fill="none"/><path d="M10 10l5 5" stroke="#333" stroke-width="2.4"/></svg>
    </div>
    <div class="btn-search">SEARCH</div>
  </form>
</section>

<section class="wrap categories">
  <div class="cat" style="width:202px"><span class="tick"><svg width="12" height="10" viewBox="0 0 12 10"><path d="M1 5l3.5 3.5L11 1.5" stroke="#fff" stroke-width="2.2" fill="none"/></svg></span><div><h3>RETAIL MALLS</h3><p>Centrally Air-Conditioned</p></div></div>
  <div class="cat" style="width:260px"><span class="tick"><svg width="12" height="10" viewBox="0 0 12 10"><path d="M1 5l3.5 3.5L11 1.5" stroke="#fff" stroke-width="2.2" fill="none"/></svg></span><div><h3>SHOPPING COMPLEX</h3><p>Non Air-Conditioned Building</p></div></div>
  <div class="cat" style="width:260px"><span class="tick"><svg width="12" height="10" viewBox="0 0 12 10"><path d="M1 5l3.5 3.5L11 1.5" stroke="#fff" stroke-width="2.2" fill="none"/></svg></span><div><h3>HIGH STREET SHOPS</h3><p>Road Facing Retail</p></div></div>
  <div class="cat" style="width:242px;padding-left:30px"><span class="tick"><svg width="12" height="10" viewBox="0 0 12 10"><path d="M1 5l3.5 3.5L11 1.5" stroke="#fff" stroke-width="2.2" fill="none"/></svg></span><div><h3>RETAIL WAREHOUSES</h3><p>Back-end Retail Storage</p></div></div>
</section>

<section class="wrap projects" style="top:992px;height:308px">
  <h2>FEATURED PROJECTS</h2>
  <span class="more"><svg width="9" height="8" viewBox="0 0 9 8"><path d="M5 0l4 4-4 4V5H0V3h5z" fill="#666"/></svg></span>
  <div class="cards">
    <div class="card"><div class="thumb" role="img" aria-label="Photo of a shopping complex" style="background:linear-gradient(#9fb5c8,#7f8f7a 60%,#5a6356)"></div><div class="name">Veltrona Arcade</div><div class="city">SURAT</div><div class="type">Shopping Complex</div></div>
    <div class="card"><div class="thumb" role="img" aria-label="Photo of a shopping complex" style="background:linear-gradient(#1f3657,#4d5e78 55%,#8a7d6a)"></div><div class="name">Veltrona Arcade</div><div class="city">SURAT</div><div class="type">Shopping Complex</div></div>
    <div class="card"><div class="thumb" role="img" aria-label="Photo of a shopping complex" style="background:linear-gradient(#4d8fd0,#a9cbe6 50%,#d9dfe3)"></div><div class="name">Veltrona Arcade</div><div class="city">SURAT</div><div class="type">Shopping Complex</div></div>
    <div class="card"><div class="thumb" role="img" aria-label="Photo of a shopping complex" style="background:linear-gradient(#1d2e66,#394a80 50%,#a07a3e)"></div><div class="name">Veltrona Arcade</div><div class="city">SURAT</div><div class="type">Shopping Complex</div></div>
    <div class="card"><div class="thumb" role="img" aria-label="Photo of a shopping complex" style="background:linear-gradient(#3c4d6e,#6d6f7a 55%,#8d5a4a)"></div><div class="name">Veltrona Arcade</div><div class="city">SURAT</div><div class="type">Shopping Complex</div></div>
  </div>
</section>

<section class="wrap projects" style="top:1312px;height:308px">
  <h2>NEW LAUNCHES</h2>
  <span class="more"><svg width="9" height="8" viewBox="0 0 9 8"><path d="M5 0l4 4-4 4V5H0V3h5z" fill="#666"/></svg></span>
  <div class="cards">
    <div class="card"><div class="thumb" role="img" aria-label="Photo of a shopping complex" style="background:linear-gradient(#c8d0d6,#9a7d78 55%,#6b5a55)"></div><div class="name">Veltrona Arcade</div><div class="city">SURAT</div><div class="type">Shopping Complex</div></div>
    <div class="card"><div class="thumb" role="img" aria-label="Photo of a shopping complex" style="background:linear-gradient(#27466e,#4e7aa6 55%,#3a4048)"></div><div class="name">Veltrona Arcade</div><div class="city">SURAT</div><div class="type">Shopping Complex</div></div>
    <div class="card"><div class="thumb" role="img" aria-label="Photo of a shopping complex" style="background:linear-gradient(#9cc3e4,#b3b9ba 55%,#6d7566)"></div><div class="name">Veltrona Arcade</div><div class="city">SURAT</div><div class="type">Shopping Complex</div></div>
    <div class="card"><div class="thumb" role="img" aria-label="Photo of a shopping complex" style="background:linear-gradient(#bcd2e6,#b79a8d 55%,#8a8278)"></div><div class="name">Veltrona Arcade</div><div class="city">SURAT</div><div class="type">Shopping Complex</div></div>
    <div class="card"><div class="thumb" role="img" aria-label="Photo of a shopping complex" style="background:linear-gradient(#5f8a58,#3f607d 50%,#7a8a95)"></div><div class="name">Veltrona Arcade</div><div class="city">SURAT</div><div class="type">Shopping Complex</div></div>
  </div>
</section>

<section class="wrap projects" style="top:1633px;height:307px">
  <h2>EDITOR'S CHOICE</h2>
  <span class="more"><svg width="9" height="8" viewBox="0 0 9 8"><path d="M5 0l4 4-4 4V5H0V3h5z" fill="#666"/></svg></span>
  <div class="cards">
    <div class="card"><div class="thumb" role="img" aria-label="Photo of a shopping complex" style="background:linear-gradient(#4f86c6,#c9d3df 55%,#8a8f96)"></div><div class="name">Veltrona Arcade</div><div class="city">SURAT</div><div class="type">Shopping Complex</div></div>
    <div class="card"><div class="thumb" role="img" aria-label="Photo of a shopping complex" style="background:linear-gradient(#5d9bd8,#e4ecf2 55%,#9ba3a8)"></div><div class="name">Veltrona Arcade</div><div class="city">SURAT</div><div class="type">Shopping Complex</div></div>
    <div class="card"><div class="thumb" role="img" aria-label="Photo of a shopping complex" style="background:linear-gradient(#101828,#3b2a2a 55%,#b3482e)"></div><div class="name">Veltrona Arcade</div><div class="city">SURAT</div><div class="type">Shopping Complex</div></div>
    <div class="card"><div class="thumb" role="img" aria-label="Photo of a shopping complex" style="background:linear-gradient(#3a5e9a,#c89a6a 55%,#4d6a3f)"></div><div class="name">Veltrona Arcade</div><div class="city">SURAT</div><div class="type">Shopping Complex</div></div>
    <div class="card"><div class="thumb" role="img" aria-label="Photo of a shopping complex" style="background:linear-gradient(#d6d8da,#8d8f92 55%,#4a4c50)"></div><div class="name">Veltrona Arcade</div><div class="city">SURAT</div><div class="type">Shopping Complex</div></div>
  </div>
</section>

<section class="newsletter">
  <h2>NEWS LETTER</h2>
  <div class="input" style="left:333px;width:208px">Email ID</div>
  <div class="input dd" style="left:548px;width:207px">Select Option</div>
  <div class="input dd" style="left:763px;width:206px">Adilabad</div>
  <div class="btn-subscribe">Subscribe</div>
</section>

<footer class="site-footer">
  <div class="fcol" style="left:119px">
    <h4>About Retail Nexus</h4>
    <div style="display:flex;gap:22px">
      <ul><li>About Us</li><li>Privacy Policy</li><li>Terms of Use</li><li>Contact Us</li><li>Site Map</li></ul>
      <ul><li>Retail Malls</li><li>Shopping Complex</li><li>High Street Shops</li><li>Retail Warehouses</li></ul>
    </div>
  </div>
  <div class="fcol sep" style="left:367px">
    <h4 style="margin-bottom:12px">About us</h4>
    <p class="about">Sed nec enim tempus, porta mi ut, auctor neque. Aliquam ut velit ac nibh vestibulum laoreet. Cras condimentum ut ligula eget rhoncus. In sit amet odio consequat, lobortis neque quis.</p>
  </div>
  <div class="fcol sep" style="left:615px">
    <h4>Contact us</h4>
    <div class="contact-row"><svg width="9" height="12" viewBox="0 0 9 12"><path d="M4.5 0A4.5 4.5 0 0 0 0 4.5C0 8 4.5 12 4.5 12S9 8 9 4.5A4.5 4.5 0 0 0 4.5 0zm0 6.3a1.8 1.8 0 1 1 0-3.6 1.8 1.8 0 0 1 0 3.6z" fill="#bbb"/></svg><span>Unit 218, 2nd Floor,<br>Block-Q, Gurgaon -<br>122009</span></div>
    <div class="contact-row"><svg width="12" height="12" viewBox="0 0 12 12"><path d="M2.4 0l2 2.6-1.2 1.6c.8 1.7 2 2.9 3.7 3.7L8.4 6.7 11 8.6 9.8 11C4.6 11 0 6.4 0 1.2z" fill="#bbb"/></svg><span>Phone: 555 014 2290</span></div>
    <div class="contact-row"><svg width="12" height="9" viewBox="0 0 12 9"><rect width="12" height="9" fill="#bbb"/><path d="M0 0l6 5 6-5" stroke="#2f2f31" fill="none"/></svg><span>info@lotstallmart.com</span></div>
  </div>
  <form class="wizard-form">
    <h4>Mart Wizards</h4>
    <div class="f-input">Name</div>
    <div class="f-input">E-mail</div>
    <div class="f-input">Comment</div>
    <div class="btn-submit">SUBMIT</div>
  </form>
</footer>

<div class="bottom-bar">
  <p>Copyright © 2014 Lotstallmart. &nbsp;All rights reserved.</p>
  <div class="social"><span></span><span></span><span></span><span></span><span></span><span></span></div>
</div>

</body>
</html>
```